IT Management and Consulting company wants a design

The website should transfer an innovative, forward-oriented, optimistic, and serious image to my customer. Because we work in an agile, the design should transfer this approach.

The new color should make a serious, but not boring, impression for the business visitors of top-level companies.

The main focus topics are:
* IT strategy consulting
* Digital transformation
* IT quality management

The website should be in the English language.

The website should be created for WordPress. The existing website is http://www.v-tek.com (no WordPress) is provided by servplanet.de. A WordPress sandbox system exists.

Target Market(s)

Purchasing departments, IT decision makers from companies, project recruiting companies

Industry/Entity Type

IT-Provider, Telecommunication, Automotive

Number of Pages Required

4 page

Font styles to use
Serif
Sans Serif

Requirements
Must have
• Long-pager scrolling, a detail page for each portfolio topics, contact page, page about the company
Nice to have
• Parallax animation less is more, maybe a nice Hero Video Header, interessting 3D graph, Isometric graphs will bi nice, more clean than overloaded,
Should not have
• personal recruting page like in www.v-tek.com

```html
<!DOCTYPE html>
<html lang="en">
<head>
<meta charset="utf-8">
<title>Vantek Consulting</title>
<link rel="stylesheet" href="https://fonts.googleapis.com/css2?family=Lato:wght@400;700;900&display=swap">
<style>
:root{
  --brand:#b06a06;
  --brand-band:rgba(176,122,18,.92);
  --ink:#1c1c1c;
  --text:#444;
  --muted-bg:#efefef;
  --white:#fff;
}
*{box-sizing:border-box;margin:0;padding:0}
html,body{width:1200px;height:4228px;overflow:hidden}
body{font-family:'Lato',sans-serif;color:var(--text);background:var(--white);position:relative}
.abs{position:absolute}
.topline{left:0;top:0;width:1200px;height:6px;background:#9a9a9a}

/* header */
.brand-name{display:flex;align-items:center;gap:10px;font-weight:700;color:var(--ink);font-size:26px;line-height:1;letter-spacing:.5px}
.brand-dot{width:12px;height:12px;border-radius:50%;background:var(--brand)}
.nav{top:54px;left:486px;display:flex;align-items:center;font-size:13px;font-weight:700;color:var(--ink);letter-spacing:.3px}
.nav a{text-decoration:none;color:inherit;margin-right:42px}
.nav .active{background:var(--brand);color:#fff;width:90px;height:40px;display:flex;align-items:center;justify-content:center;margin-right:22px}
.nav .lang{color:var(--brand);margin-right:0}

/* hero */
.hero-title{left:74px;top:332px;font-size:62px;font-weight:900;line-height:70px;color:var(--ink);letter-spacing:1px}
.hero-sub{left:75px;top:484px;width:415px;font-size:23px;line-height:31px;color:var(--ink)}
.btn{background:var(--brand);color:#fff;font-weight:700;font-size:17px;display:flex;align-items:center;justify-content:center;letter-spacing:.5px}
.dots{left:75px;top:792px;display:flex;gap:9px}
.dots span{width:12px;height:12px;background:#8a8a8a;border-radius:2px}
.dots span:first-child{background:var(--brand)}
.hero-card{left:525px;top:238px;width:700px;height:506px;border-radius:18px;background:linear-gradient(135deg,#fff 0%,#f4f4f4 60%,#eaeaea 100%);box-shadow:0 6px 18px rgba(0,0,0,.18)}

/* headings */
.sec-title{font-size:33px;font-weight:900;color:var(--ink);letter-spacing:.5px}
.center{left:0;width:1200px;text-align:center}
.rule{height:3px;background:var(--brand);width:180px}
.para{font-size:17px;line-height:28px;color:var(--text)}

/* what we do */
.muted{left:0;width:1200px;background:var(--muted-bg)}
.service{width:340px;text-align:center}
.service .circle{width:102px;height:102px;border-radius:50%;background:var(--brand);margin:0 auto;display:flex;align-items:center;justify-content:center}
.service h3{color:var(--brand);font-size:19px;font-weight:900;margin-top:36px}
.service p{font-size:17px;line-height:26px;margin-top:10px}

/* portfolio */
.pcard{width:511px;height:353px;overflow:hidden}
.pcard .photo{width:100%;height:100%}
.pcard .band{position:absolute;left:0;bottom:0;width:100%;height:93px;background:var(--brand-band);color:#fff;text-align:center;padding-top:20px}
.pcard h3{font-size:19px;font-weight:900;letter-spacing:.3px}
.pcard p{font-size:16px;margin-top:6px}

/* testimonial */
.testimonial{left:0;top:2901px;width:1200px;height:366px;background:linear-gradient(100deg,#243244 0%,#33465b 45%,#1a2431 100%)}
.quote-mark{font-size:110px;font-weight:900;color:var(--brand);line-height:1}
.quote-text{color:#fff;font-size:17px;line-height:29px}
.quote-name{color:#fff;font-weight:700;font-size:17px;letter-spacing:.5px}

/* blog */
.post{width:331px}
.post .thumb{width:331px;height:189px;position:relative}
.post .date{position:absolute;left:-13px;top:128px;background:#111;color:#fff;display:flex;align-items:center;gap:6px;padding:0 8px;height:40px}
.post .date small{font-size:12px;font-weight:700;line-height:12px}
.post .date b{font-size:30px;font-weight:700}
.post h3{font-size:19px;font-weight:900;color:var(--ink);line-height:26px;margin-top:30px}
.post p{font-size:16px;line-height:28px;margin-top:6px}
.post a{display:block;margin-top:18px;font-size:15px;font-weight:900;color:var(--brand);text-decoration:none}

/* footer */
.footer{left:0;top:3917px;width:1200px;height:311px;background:var(--muted-bg)}
.fcol h4{color:var(--brand);font-size:17px;font-weight:900}
.fcol ul{list-style:none;margin-top:10px}
.fcol li{font-size:14px;line-height:31px;color:#333}
.small{font-size:14px;line-height:25px;color:#333}
.social{display:flex;gap:18px}
.social span{width:20px;height:20px;border-radius:50%;background:#222}
.input{width:243px;height:41px;background:#fff;font-size:14px;color:#555;padding:0 14px;display:flex;align-items:center}
</style>
</head>
<body>
<div class="abs topline"></div>

<header>
  <div class="abs brand-name" style="left:74px;top:62px"><span class="brand-dot"></span>Vantek Consulting</div>
  <nav class="abs nav">
    <a class="active">HOME</a><a>COMPANIES</a><a>PORTFOLIOS</a><a>SCOUTING</a><a>CONTACT</a><a class="lang">EN &#8964;</a>
  </nav>
</header>

<section class="hero">
  <svg class="abs" style="left:0;top:0" width="1200" height="860" aria-hidden="true">
    <path d="M608 136 H1200 V240 H626 L591 158 Q586 136 608 136Z" fill="var(--brand)"/>
    <path d="M690 740 H1200 V847 H740 Q718 847 712 828Z" fill="var(--brand)"/>
  </svg>
  <div class="abs hero-card" role="img" aria-label="Illustration of two consultants presenting dashboard windows and charts"></div>
  <h1 class="abs hero-title">VANTEK<br>CONSULTING</h1>
  <p class="abs hero-sub">We are a IT project management, consulting, commissioning management or system integration.</p>
  <div class="abs btn" style="left:75px;top:607px;width:181px;height:41px">READ MORE</div>
  <div class="abs dots"><span></span><span></span><span></span><span></span></div>
</section>

<section class="welcome">
  <div class="abs" style="left:0;top:960px;width:591px;height:290px;background:linear-gradient(180deg,#fafafa,#ececec)" role="img" aria-label="Illustration of two people working together at a desk with a monitor and documents"></div>
  <h2 class="abs sec-title" style="left:614px;top:934px;line-height:39px">WELCOME TO<br>VANTEK CONSULTING</h2>
  <div class="abs rule" style="left:614px;top:1028px"></div>
  <p class="abs para" style="left:614px;top:1051px;width:520px">Lorem ipsum dolor sit amet, consectetur adipiscing elit semper tristique nunc non pellentesque scelerisque, neque dictum convallis maximus, nulla mi dignissim lectus, id porta tortor ante eu libero metus id orci egestas efficitur. Duis ac lacinia nunc, quis luctus magna risus sapien.</p>
  <div class="abs btn" style="left:614px;top:1221px;width:180px;height:50px">READ MORE</div>
</section>

<section class="abs muted" style="top:1359px;height:567px">
  <h2 class="abs sec-title center" style="top:71px">WHAT WE DO</h2>
  <div class="abs rule" style="left:511px;top:135px"></div>
  <p class="abs para center" style="top:168px;padding:0 90px;line-height:25px">Lorem ipsum dolor sit amet, consectetur adipiscing elit. Sed semper tristique nunc non pellentesque. neque dictum convallis maximus,<br>nulla mi dignissim lectus, id porta tortor ante eu libero.</p>

  <div class="abs service" style="left:70px;top:256px">
    <div class="circle"><svg width="44" height="52" viewBox="0 0 44 52"><path d="M22 2a18 18 0 0 0-10 33v6h20v-6A18 18 0 0 0 22 2z" fill="#fff"/><rect x="14" y="43" width="16" height="4" rx="2" fill="#fff"/><rect x="17" y="48" width="10" height="3" rx="1.5" fill="#fff"/></svg></div>
    <h3>IT STRATEGY CONSULTING</h3>
    <p>Lorem ipsum dolor sit amet,<br>consectetur adipiscing elit semper<br>tristique nunc non.</p>
  </div>
  <div class="abs service" style="left:430px;top:256px">
    <div class="circle"><svg width="56" height="48" viewBox="0 0 56 48"><circle cx="20" cy="24" r="13" fill="none" stroke="#fff" stroke-width="8" stroke-dasharray="5 3.2"/><circle cx="20" cy="24" r="5" fill="#fff"/><circle cx="43" cy="13" r="7" fill="none" stroke="#fff" stroke-width="5" stroke-dasharray="3 2"/><circle cx="43" cy="36" r="7" fill="none" stroke="#fff" stroke-width="5" stroke-dasharray="3 2"/></svg></div>
    <h3>DIGITAL TRANSFORMATION</h3>
    <p>Lorem ipsum dolor sit amet,<br>consectetur adipiscing elit semper<br>tristique nunc non.</p>
  </div>
  <div class="abs service" style="left:789px;top:256px">
    <div class="circle"><svg width="48" height="48" viewBox="0 0 48 48"><rect x="4" y="20" width="10" height="24" rx="2" fill="#fff"/><path d="M17 21l9-16c4 0 6 3 5 7l-2 7h12c3 0 5 3 4 6l-4 15c-1 2-3 4-5 4H17z" fill="#fff"/></svg></div>
    <h3>IT QUALITY MANAGEMENT</h3>
    <p>Lorem ipsum dolor sit amet,<br>consectetur adipiscing elit semper<br>tristique nunc non.</p>
  </div>
</section>

<section class="portfolio">
  <h2 class="abs sec-title center" style="top:1990px">OUR PORTFOLIO</h2>
  <div class="abs rule" style="left:511px;top:2049px"></div>
  <div class="abs pcard" style="left:74px;top:2101px">
    <div class="photo" role="img" aria-label="Photo of a team reviewing data on screens" style="background:linear-gradient(120deg,#2b2a24,#6b5a3d 40%,#3a4a52 75%,#cfd6d8)"></div>
    <div class="band"><h3>PROJECTS IN EXCELLENCE</h3><p>Excepteur sint occaecat cupidatat non</p></div>
  </div>
  <div class="abs pcard" style="left:617px;top:2101px">
    <div class="photo" role="img" aria-label="Photo of consultants talking in a server room" style="background:linear-gradient(120deg,#0f2a48,#2e5a86 50%,#10263f)"></div>
    <div class="band"><h3>CONSULTING IN EXCELLENCE</h3><p>Excepteur sint occaecat cupidatat non</p></div>
  </div>
  <div class="abs pcard" style="left:74px;top:2484px">
    <div class="photo" role="img" aria-label="Photo of digital cloud and device icons on a blue background" style="background:linear-gradient(120deg,#1b4f7a,#4f8fb8 50%,#bcd9ea)"></div>
    <div class="band"><h3>CLOUD TRANSITION</h3><p>Excepteur sint occaecat cupidatat non</p></div>
  </div>
  <div class="abs pcard" style="left:617px;top:2484px">
    <div class="photo" role="img" aria-label="Photo of a hand drawing a digitalization progress bar" style="background:linear-gradient(120deg,#0c2f6b,#2f74c0 50%,#e0a98e)"></div>
    <div class="band"><h3>DIGITALIZATION</h3><p>Excepteur sint occaecat cupidatat non</p></div>
  </div>
</section>

<section class="abs testimonial" role="img" aria-label="Dark photo of a person working on a tablet with charts">
  <div class="abs quote-mark center" style="top:54px">&ldquo;</div>
  <p class="abs quote-text center" style="top:133px">&ldquo; Lorem ipsum dolor sit amet, consectetur adipiscing elit semper<br>tristique nunc non pellentesque scelerisque, neque dictum convallis maximus, nulla mi dignissim<br>lectus, id porta tortor ante eu libero orci egestas efficitur. Duis ac lacinia nunc, quis luctus<br>magna ipsum dolor sit amet, consectetur adipiscing elit..&rdquo;</p>
  <div class="abs quote-name center" style="top:258px">NAME HEADING</div>
</section>

<section class="blog">
  <h2 class="abs sec-title center" style="top:3325px">BLOG POSTS</h2>
  <div class="abs rule" style="left:511px;top:3390px"></div>
  <article class="abs post" style="left:74px;top:3439px">
    <div class="thumb" role="img" aria-label="Photo of two colleagues at a whiteboard with sticky notes" style="background:linear-gradient(120deg,#4a4036,#8ea7b3 45%,#c9b79d)"><div class="date"><small>SEP<br>2021</small><b>25</b></div></div>
    <h3>SED SEMPER TRISTIQUE NUNC<br>NON PELLENTESQUE</h3>
    <p>Lorem ipsum dolor sit amet, consectetur adipiscing elit semper tristique nunc non pellentesque scelerisque..</p>
    <a>READ MORE</a>
  </article>
  <article class="abs post" style="left:435px;top:3439px">
    <div class="thumb" role="img" aria-label="Photo of a hand touching a digital network interface" style="background:linear-gradient(120deg,#15345e,#3f75ad 50%,#9cc0de)"><div class="date"><small>SEP<br>2021</small><b>10</b></div></div>
    <h3>SED SEMPER TRISTIQUE NUNC<br>NON PELLENTESQUE</h3>
    <p>Lorem ipsum dolor sit amet, consectetur adipiscing elit semper tristique nunc non pellentesque scelerisque..</p>
    <a>READ MORE</a>
  </article>
  <article class="abs post" style="left:796px;top:3439px">
    <div class="thumb" role="img" aria-label="Photo of a team joining hands over a desk" style="background:linear-gradient(120deg,#3a3a3a,#8d7a66 50%,#d9d2c8)"><div class="date"><small>SEP<br>2021</small><b>10</b></div></div>
    <h3>SED SEMPER TRISTIQUE NUNC<br>NON PELLENTESQUE</h3>
    <p>Lorem ipsum dolor sit amet, consectetur adipiscing elit semper tristique nunc non pellentesque scelerisque..</p>
    <a>READ MORE</a>
  </article>
</section>

<footer class="abs footer">
  <div class="abs brand-name" style="left:74px;top:78px;font-size:22px"><span class="brand-dot"></span>Vantek Consulting</div>
  <p class="abs small" style="left:74px;top:143px">Copyright &copy; 2021. Company Name<br>All Right Reserved</p>
  <div class="abs social" style="left:74px;top:210px"><span></span><span></span><span></span><span></span><span></span></div>

  <div class="abs fcol" style="left:417px;top:52px"><h4>SITE MAP</h4><ul><li>Home</li><li>Companies</li><li>Portfolios</li><li>Scouting</li><li>Contact</li></ul></div>
  <div class="abs fcol" style="left:630px;top:52px"><h4>PORTFOLIO</h4><ul><li>Projects in Excellence</li><li>Consulting in Excellence</li><li>Digitalization</li><li>Cloud transition</li></ul></div>
  <div class="abs fcol" style="left:883px;top:52px"><h4>EMAIL SIGN UP</h4></div>
  <div class="abs input" style="left:883px;top:85px">Enter Name</div>
  <div class="abs input" style="left:883px;top:139px">Enter Email Address</div>
  <div class="abs btn" style="left:1036px;top:200px;width:90px;height:40px;font-size:15px">SIGN UP</div>
</footer>
</body>
</html>
```